Fun relaxed Travel Photography Business Card*

Require a fun, funky and quirky but rememberable business card for a travel photographer

Industry/Entity Type

Photographer

Contact Information for Business Card

Front Card

(my name) Lenn D.

Travel Photographer ( small under travel photographer) “self-proclaimed”

(website logo) wanderingsoflenn.net

(Instagram logo) @wanderings_of_lenn

(Instagram logo) @wanderings_of_lenn_2.0 (backup for when Instagram puts Lenn on timeout for bad behaviour)

Tel: N/A (removing the potential awkwardness of me not replying)

Email: (see above)

Back Card

Offending people since 1986

(Bottom right corner) “p.s. travelling made me fatTER”

Font styles to use
Serif

Colors

Designer to choose colors to be used in the design.

Requirements
Must have
• a camera
• a similar cartoon version of me as the "logo" see attached files, try to make as similar as possible

```html
<!DOCTYPE html>
<html lang="en">
<head>
<meta charset="utf-8">
<title>Lenn D. — Travel Photographer Business Card</title>
<link rel="stylesheet" href="https://fonts.googleapis.com/css2?family=Roboto:wght@400;500&display=swap">
<style>
  :root {
    --stage: #4a220b;
    --card: #29363d;
    --band: #512f20;
    --gold: #f0b52e;
    --ink-light: #f1f1f1;
    --art-warm: #e8a82a;
    --art-deep: #b5761c;
  }
  * { box-sizing: border-box; margin: 0; padding: 0; }
  html, body {
    width: 1200px;
    height: 1200px;
    overflow: hidden;
    background: var(--stage);
    font-family: "Roboto", Arial, sans-serif;
  }
  .stage {
    position: relative;
    width: 1200px;
    height: 1200px;
    display: flex;
    flex-direction: column;
    align-items: center;
    justify-content: center;
    gap: 72px;
  }
  .card {
    position: relative;
    width: 900px;
    height: 486px;
    background: var(--card);
    border-radius: 6px;
    overflow: hidden;
    box-shadow: 0 14px 30px rgba(0,0,0,0.45);
  }
  .card-bands {
    position: absolute;
    inset: 0;
    width: 100%;
    height: 100%;
  }
  .mascot-art {
    position: absolute;
    top: 30px;
    right: 40px;
    width: 220px;
    height: 270px;
    border-radius: 24px;
    background: linear-gradient(160deg, var(--art-warm), var(--art-deep));
  }
  .identity {
    position: absolute;
    left: 62px;
    top: 208px;
    line-height: 1.1;
  }
  .identity-name {
    color: var(--gold);
    font-size: 34px;
    font-weight: 400;
    letter-spacing: 1px;
    text-transform: uppercase;
  }
  .identity-title {
    color: var(--ink-light);
    font-size: 26px;
    font-weight: 400;
    letter-spacing: 0.5px;
  }
  .identity-note {
    color: var(--ink-light);
    font-size: 18px;
  }
  .contacts {
    position: absolute;
    left: 420px;
    top: 350px;
    list-style: none;
  }
  .contact {
    display: flex;
    align-items: center;
    gap: 14px;
    color: var(--ink-light);
    font-size: 19px;
    height: 32px;
  }
  .contact-mark {
    width: 18px;
    height: 18px;
    flex: none;
  }
  .contact-dot {
    width: 16px;
    height: 16px;
    border-radius: 50%;
    background: var(--ink-light);
    flex: none;
    margin: 0 1px;
  }
  .card-back .motto {
    position: absolute;
    left: 0;
    right: 0;
    top: 210px;
    text-align: center;
    color: var(--gold);
    font-size: 40px;
    font-weight: 400;
    letter-spacing: 1px;
  }
  .card-back .postscript {
    position: absolute;
    right: 56px;
    bottom: 60px;
    color: var(--gold);
    font-size: 20px;
  }
</style>
</head>
<body>
<main class="stage">

  <section class="card card-front" aria-label="Business card front">
    <svg class="card-bands" viewBox="0 0 900 486" preserveAspectRatio="none" aria-hidden="true">
      <polygon points="480,0 900,0 900,110" fill="var(--band)"/>
      <polygon points="0,430 560,260 900,260 900,486 0,486" fill="var(--band)"/>
    </svg>

    <div class="mascot-art" role="img" aria-label="Cartoon of the photographer in sunglasses and a floral shirt lounging in a yellow chair beside a small table with a drink"></div>

    <div class="identity">
      <h1 class="identity-name">Lenn D.</h1>
      <p class="identity-title">TRAVEL PHOTOGRAPHER</p>
      <p class="identity-note">self-proclaimed</p>
    </div>

    <ul class="contacts">
      <li class="contact">
        <svg class="contact-mark" viewBox="0 0 20 20" aria-hidden="true">
          <circle cx="10" cy="10" r="8.5" fill="none" stroke="var(--ink-light)" stroke-width="1.6"/>
          <ellipse cx="10" cy="10" rx="3.8" ry="8.5" fill="none" stroke="var(--ink-light)" stroke-width="1.4"/>
          <line x1="1.5" y1="10" x2="18.5" y2="10" stroke="var(--ink-light)" stroke-width="1.4"/>
        </svg>
        <span>wanderingsoflenn.net</span>
      </li>
      <li class="contact">
        <span class="contact-dot" aria-hidden="true"></span>
        <span>@wanderings_of_lenn</span>
      </li>
      <li class="contact">
        <span class="contact-dot" aria-hidden="true"></span>
        <span>@wanderings_of_lenn_2.0</span>
      </li>
    </ul>
  </section>

  <section class="card card-back" aria-label="Business card back">
    <p class="motto">OFFENDING PEOPLE SINCE 1986</p>
    <p class="postscript">p.s. travelling made me fatTER</p>
  </section>

</main>
</body>
</html>
```